Business card design for holistic health care clinic

We need a double-sided business card design for our holistic health care clinic that integrates our logo design and also its color scheme. My business is called Valmira. It is an integrative medicine clinic. You have already done the logo for me. Please ensure an elegant and upscale design that is not cluttered, but still has all the necessary information (please see below for details).

Target Market(s)

Wellness, fitness, rehabilitation for educated, well-traveled open-minded clients who are focused on natural, organic, balanced and preventive healthcare and lifestyle.

Industry/Entity Type

Medical

Contact Information for Business Card

Modern, clean.

Number of Pages Required

1 page

Font styles to use
Serif
Sans Serif

Colors

Designer to choose colors to be used in the design.

Requirements
Must have
• Logo on one side, all other information on the other side.
• Other information should include:
• Tobias Wrenfeld - DOE, CPT, LMT
• 4100 East Marrow Drive
• Austin, TX 78119
• 512 555 0148
• 818 555 0192
• info@ValmiraHealth.example
• t.wrenfeld@ValmiraHealth.example
Nice to have
• Darker background on front - but not totally black - shaded/dark gray.

```html
<!DOCTYPE html>
<html lang="en">
<head>
<meta charset="utf-8">
<title>Valmira business card</title>
<link rel="stylesheet" href="https://fonts.googleapis.com/css2?family=Roboto:wght@400&family=Roboto+Condensed:wght@700&display=swap">
<style>
  :root {
    --backdrop: #5a4a3c;
    --card-top: #2c2c2d;
    --card-bottom: #222223;
    --brand-blue: #0a8bc8;
    --text-light: #e6e6e6;
  }
  * { margin: 0; padding: 0; box-sizing: border-box; }
  html, body { width: 1200px; height: 960px; overflow: hidden; }
  body {
    background: var(--backdrop);
    position: relative;
    font-family: "Roboto", Arial, sans-serif;
  }
  .card {
    position: absolute;
    width: 600px;
    height: 342px;
    border-radius: 22px;
    background: linear-gradient(180deg, var(--card-top), var(--card-bottom));
  }
  .card--front { left: 315px; top: 115px; }
  .card--back  { left: 312px; top: 473px; }

  .brand-name {
    font-family: "Roboto Condensed", Arial, sans-serif;
    font-weight: 700;
    color: var(--brand-blue);
    letter-spacing: 1px;
    line-height: 1;
    text-transform: uppercase;
  }
  .brand-descriptor {
    font-family: "Roboto", Arial, sans-serif;
    font-weight: 400;
    color: var(--brand-blue);
    line-height: 1;
  }
  .card--front .brand-name { position: absolute; left: 33px; top: 76px; font-size: 50px; }
  .card--front .brand-descriptor { position: absolute; left: 36px; top: 127px; font-size: 15px; }

  .holder {
    position: absolute;
    right: 36px;
    top: 190px;
    font-family: "Roboto Condensed", Arial, sans-serif;
    font-weight: 700;
    color: var(--brand-blue);
    text-transform: uppercase;
    font-size: 21px;
    white-space: nowrap;
  }
  .holder__credentials { font-size: 13px; }
  .accent-tab {
    position: absolute;
    right: 0;
    top: 182px;
    width: 15px;
    height: 33px;
    background: var(--brand-blue);
  }
  .divider {
    position: absolute;
    left: 205px;
    right: 36px;
    top: 239px;
    height: 1px;
    background: linear-gradient(90deg, rgba(10,139,200,0), var(--brand-blue));
  }
  .contact-list {
    position: absolute;
    left: 34px;
    top: 236px;
    list-style: none;
    color: var(--text-light);
    font-size: 14.5px;
  }
  .contact-list li { display: flex; align-items: center; height: 19px; }
  .contact-list svg { width: 13px; height: 13px; margin-right: 9px; fill: var(--brand-blue); }
  .address {
    position: absolute;
    right: 36px;
    top: 255px;
    text-align: right;
    color: var(--text-light);
    font-size: 14.5px;
    line-height: 19px;
    font-style: normal;
  }

  .card--back .brand-lockup {
    position: absolute;
    left: 0; right: 0;
    top: 140px;
    text-align: center;
  }
  .card--back .brand-name { font-size: 64px; }
  .card--back .brand-descriptor { font-size: 18px; margin-top: 6px; }
  .tagline {
    position: absolute;
    left: 0; right: 0;
    top: 281px;
    text-align: center;
    color: #f2f2f2;
    font-size: 14.5px;
  }
</style>
</head>
<body>
  <section class="card card--front">
    <div class="brand-name">Valmira</div>
    <div class="brand-descriptor">Integrative Holistic Medicine</div>

    <div class="holder">Tobias Wrenfeld <span class="holder__credentials">- DOE, CPT, LMT</span></div>
    <div class="accent-tab"></div>
    <div class="divider"></div>

    <ul class="contact-list">
      <li><svg viewBox="0 0 16 16"><path d="M3.6 1l2.6 3-1.5 1.8c.9 2 2.5 3.6 4.5 4.5L11 8.8l3 2.6-1.4 2.9C7 14.2 1.8 9 1 3.1z"/></svg>512 555 0148</li>
      <li><svg viewBox="0 0 16 16"><path d="M4 0h8v16H4zM5.5 2v10h5V2zM7 13.2v1.2h2v-1.2z"/></svg>818 555 0192</li>
      <li><svg viewBox="0 0 16 16"><path d="M1 3h14v1L8 8.5 1 4zM1 5.5l7 4.5 7-4.5V13H1z"/></svg>t.wrenfeld@ValmiraHealth.example</li>
      <li><svg viewBox="0 0 16 16"><circle cx="8" cy="8" r="7"/><path d="M4 5c2 0 3 1 2 3s1 3 0 5M10 2c-1 2 1 3 3 3" stroke="#2a2a2b" stroke-width="1.2" fill="none"/></svg>www.ValmiraHealth.example</li>
    </ul>

    <address class="address">info@ValmiraHealth.example<br>4100 East Marrow Drive<br>Austin, TX 78119</address>
  </section>

  <section class="card card--back">
    <div class="brand-lockup">
      <div class="brand-name">Valmira</div>
      <div class="brand-descriptor">Integrative Holistic Medicine</div>
    </div>
    <p class="tagline">it’s all about you – your health, your objectives</p>
  </section>
</body>
</html>
```